Business card for medical clinic

I need an upmarket, modern medical/health business card for my clinic

Contact Information for Business Card

name, address, email, qr code

```html
<!DOCTYPE html>
<html lang="en">
<head>
<meta charset="utf-8">
<title>Meridian Care Clinic – Business Card</title>
<link rel="stylesheet" href="https://fonts.googleapis.com/css2?family=Cinzel:wght@400&family=Arimo:wght@400&display=swap">
<style>
  :root {
    --backdrop: #2a2a2a;
    --card-white: #ffffff;
    --blue-glow: #05a9e4;
    --blue-mid: #0b5d92;
    --blue-deep: #1c2748;
    --brand-ink: #6fd3f5;
    --name-ink: #1f4c7a;
    --role-ink: #7c828a;
    --body-ink: #555b63;
    --icon-ink: #1f5f94;
    --rule: #8a9099;
  }
  * { box-sizing: border-box; margin: 0; padding: 0; }
  html, body { width: 1200px; height: 689px; overflow: hidden; }
  body {
    background: var(--backdrop);
    display: flex;
    align-items: center;
    justify-content: center;
    gap: 44px;
  }
  .card {
    width: 520px;
    height: 297px;
    border-radius: 20px;
    overflow: hidden;
    position: relative;
  }
  /* Front */
  .card-front {
    background: radial-gradient(ellipse 60% 70% at 52% 50%, var(--blue-glow) 0%, var(--blue-mid) 45%, var(--blue-deep) 100%);
    display: flex;
    align-items: center;
    justify-content: center;
  }
  .brand {
    display: flex;
    align-items: center;
    gap: 14px;
  }
  .brand-dot {
    width: 22px; height: 22px;
    border-radius: 50%;
    background: var(--brand-ink);
  }
  .brand-name {
    font-family: "Arimo", sans-serif;
    font-weight: 400;
    font-size: 30px;
    color: var(--brand-ink);
    line-height: 1;
  }
  /* Back */
  .card-back {
    background: var(--card-white);
    display: flex;
    align-items: center;
    justify-content: center;
    padding-left: 40px;
  }
  .identity { text-align: right; padding-right: 14px; }
  .person-name {
    font-family: "Cinzel", serif;
    font-weight: 400;
    font-size: 22px;
    color: var(--name-ink);
    letter-spacing: 0.5px;
  }
  .person-role {
    font-family: "Arimo", sans-serif;
    font-size: 12px;
    color: var(--role-ink);
    margin: 1px 0 6px;
  }
  .address {
    font-family: "Arimo", sans-serif;
    font-style: normal;
    font-size: 12.5px;
    line-height: 1.35;
    color: var(--body-ink);
  }
  .divider { width: 1px; height: 82px; background: var(--rule); }
  .contacts {
    list-style: none;
    padding-left: 12px;
    font-family: "Arimo", sans-serif;
    font-size: 12.5px;
    color: var(--body-ink);
    line-height: 1.45;
  }
  .contacts li { display: flex; align-items: center; gap: 6px; }
  .contacts svg { width: 11px; height: 11px; fill: var(--icon-ink); flex: none; }
</style>
</head>
<body>
  <section class="card card-front" aria-label="Card front">
    <div class="brand">
      <span class="brand-dot"></span>
      <span class="brand-name">Meridian Care Clinic</span>
    </div>
  </section>

  <section class="card card-back" aria-label="Card back">
    <div class="identity">
      <h1 class="person-name">Daniel Hart</h1>
      <p class="person-role">President</p>
      <address class="address">4521 Willow Court<br>Halden, Canada 28416</address>
    </div>
    <div class="divider"></div>
    <ul class="contacts">
      <li><svg viewBox="0 0 24 24"><path d="M6.6 10.8a15.1 15.1 0 0 0 6.6 6.6l2.2-2.2a1 1 0 0 1 1-.25 11.4 11.4 0 0 0 3.6.57 1 1 0 0 1 1 1V20a1 1 0 0 1-1 1A17 17 0 0 1 3 4a1 1 0 0 1 1-1h3.5a1 1 0 0 1 1 1c0 1.25.2 2.45.57 3.57a1 1 0 0 1-.25 1z"/></svg>555-210-4836</li>
      <li><svg viewBox="0 0 24 24"><path d="M7 1h10a2 2 0 0 1 2 2v18a2 2 0 0 1-2 2H7a2 2 0 0 1-2-2V3a2 2 0 0 1 2-2zm0 3v15h10V4z"/></svg>555-318-7290</li>
      <li><svg viewBox="0 0 24 24"><path d="M2 5h20v14H2zm2 2v.5l8 5 8-5V7z"/></svg>info@meridiancare.com</li>
      <li><svg viewBox="0 0 24 24"><circle cx="12" cy="12" r="10"/></svg>www.meridiancare.com</li>
    </ul>
  </section>
</body>
</html>
```